Allied Health team of Physiotherapists & Occupational Therapists seek a business card design

We have our new logo, we now need our new business cards and stationary. Tidewell: Oedema & Family Clinic is seeking a generic card design to represent our whole team and individual cards for each therapist that incorporates our new logo to communicate our holistic approach that is calming, nuturing, supportive and welcoming.
Our Physiotherapists and Occupational Therapists assess, treat and provide education for people who are at risk of or who have lymphoedema. This is often as a result of treatment for cancer. We provide pre-operative and post-operative management and cancer rehabilitation in our Pilates studio. Our team also consists of Physiotherapists who have a strong interest in pelvic floor and continence management for both men and women.

Target Market(s)

Mainly women health conscious

Industry/Entity Type

Allied Health: Physiotherapy / Occupational Therapy

Contact Information for Business Card

Address: 14 Gallivant Ave Frankston 3199 Phone: 84316570 fax: 8431 6578 Email: info@tidewellcareservices.com.au Website: tidewellcareservices.com.au Facebook address: facebook.com/TidewellOedemaAndFamilyCareClinic. Room to write appointments. Individual cards need to have name, office email and individual email and professional details

Requirements
Must have
• Logo as per uploaded documents

```html
<!DOCTYPE html>
<html lang="en">
<head>
<meta charset="utf-8">
<title>Tidewell Business Card</title>
<link href="https://fonts.googleapis.com/css2?family=Michroma&family=Open+Sans:wght@400;600&display=swap" rel="stylesheet">
<style>
  :root {
    --backdrop: #ece8e4;
    --card-white: #ffffff;
    --peach: #f8b083;
    --peach-deep: #f2a274;
    --sage: #c5cdc3;
    --ink: #2e2e2e;
    --on-peach: #ffffff;
  }
  * { margin: 0; padding: 0; box-sizing: border-box; }
  html, body {
    width: 1200px; height: 900px; overflow: hidden;
    background: var(--backdrop);
    font-family: "Open Sans", Arial, sans-serif;
  }
  .business-card {
    position: absolute; left: 80px; top: 128px;
    width: 1040px; height: 644px;
    background: var(--card-white);
    box-shadow: 0 6px 24px rgba(0,0,0,0.12);
    overflow: hidden;
  }
  .wave-art { position: absolute; inset: 0; width: 100%; height: 100%; }
  .brand-mark {
    position: absolute; left: 140px; top: 56px;
    width: 256px; height: 256px;
    display: flex; align-items: center; justify-content: center;
  }
  .brand-ring {
    position: absolute; inset: 0;
    border: 2px solid var(--peach); border-radius: 50%;
  }
  .brand-name {
    font-family: "Open Sans", Arial, sans-serif;
    font-weight: 400; font-size: 40px; color: var(--peach-deep);
  }
  .person { position: absolute; left: 142px; top: 398px; }
  .person-name {
    font-family: "Michroma", "Arial Black", sans-serif;
    font-size: 21px; letter-spacing: 3px; color: var(--peach-deep);
    line-height: 1;
  }
  .person-title { font-size: 17px; color: var(--ink); margin-top: 6px; }
  .contact-line {
    position: absolute; right: 40px;
    display: flex; align-items: center; gap: 16px;
    color: var(--on-peach); font-size: 22px;
  }
  .contact-line svg { width: 26px; height: 26px; flex: none; }
  .contact-phone { top: 412px; }
  .contact-email { top: 457px; }
  .contact-address {
    position: absolute; left: 609px; top: 535px;
    color: var(--on-peach); font-size: 22px; line-height: 34px;
  }
</style>
</head>
<body>
  <div class="business-card">
    <svg class="wave-art" viewBox="0 0 1204 745" preserveAspectRatio="none" aria-hidden="true">
      <path fill="var(--sage)" d="M0,455 C120,560 260,605 430,565 C630,515 820,325 1000,310 C1100,302 1170,345 1204,392 L1204,745 L0,745 Z"/>
      <path fill="var(--card-white)" d="M0,478 C125,585 265,625 432,588 C635,540 822,355 1000,342 C1100,335 1170,375 1204,400 L1204,745 L0,745 Z"/>
      <path fill="var(--peach)" d="M0,492 C130,600 270,648 436,606 C640,556 825,372 1000,358 C1100,350 1170,390 1204,408 L1204,745 L0,745 Z"/>
    </svg>

    <div class="brand-mark">
      <span class="brand-ring"></span>
      <span class="brand-name">Tidewell</span>
    </div>

    <div class="person">
      <p class="person-name">CLARA WENDT</p>
      <p class="person-title">CEO/Managing Director</p>
    </div>

    <div class="contact-line contact-phone">
      <span>214-555-0147</span>
      <svg viewBox="0 0 24 24" fill="none" stroke="#fff" stroke-width="1.8" stroke-linejoin="round">
        <path d="M5 3h4l2 5-2.5 1.5a11 11 0 0 0 6 6L16 13l5 2v4a2 2 0 0 1-2 2A16 16 0 0 1 3 5a2 2 0 0 1 2-2z"/>
      </svg>
    </div>
    <div class="contact-line contact-email">
      <span>clarawendt@emailaddress.com</span>
      <svg viewBox="0 0 24 24" fill="none" stroke="#fff" stroke-width="1.8" stroke-linejoin="round">
        <rect x="2" y="5" width="20" height="14"/>
        <path d="M2 5l10 8 10-8M2 19l7-6M22 19l-7-6"/>
      </svg>
    </div>
    <div class="contact-address">
      318 Harlow Avenue NW Suite<br>210.Alder Falls Mi 48871
    </div>
  </div>
</body>
</html>
```